business card design for a plumbing contractor

i need a double business card for a plumbing business, our initial service is residential Sewer Drain Cleaning.

Target Market(s)

other plumbing Business

Industry/Entity Type

Plumbing

Contact Information for Business Card

www.PipeworksTopMark.example- 5307218394-

Font styles to use
Serif

Colors
ec1f27
0455a3

```html
<!DOCTYPE html>
<html lang="en">
<head>
<meta charset="utf-8">
<title>Pipeworks TopMark – Business Card</title>
<link rel="stylesheet" href="https://fonts.googleapis.com/css2?family=Roboto+Condensed:wght@400;700&family=Roboto:wght@400&display=swap">
<style>
  :root {
    --backdrop: #2b2b2b;
    --brand-red: #d63830;
    --card-white: #f1f1f1;
    --brand-taupe: #877f72;
    --logo-grey: #6f675d;
    --ink-light: #ffffff;
  }
  * { margin: 0; padding: 0; box-sizing: border-box; }
  html, body {
    width: 1200px;
    height: 960px;
    overflow: hidden;
    background: var(--backdrop);
  }
  .card {
    position: absolute;
    width: 600px;
    height: 342px;
    box-shadow: 0 2px 4px rgba(0,0,0,0.45);
  }
  .card--front { left: 322px; top: 108px; display: flex; }
  .card--back  { left: 320px; top: 493px; background: var(--brand-taupe);
                 display: flex; align-items: center; justify-content: center; }

  .contact-panel {
    width: 275px;
    height: 100%;
    background: var(--brand-red);
    color: var(--ink-light);
    padding: 84px 0 0 23px;
  }
  .contact-panel__name {
    font: 700 23px/1 "Roboto Condensed", sans-serif;
    letter-spacing: 0.3px;
  }
  .contact-panel__role {
    font: 700 15px/1 "Roboto Condensed", sans-serif;
    letter-spacing: 0.5px;
    margin-top: 5px;
  }
  .contact-panel__details {
    list-style: none;
    margin-top: 14px;
    font: 400 13.5px/18px "Roboto Condensed", sans-serif;
  }
  .contact-panel__services {
    list-style: none;
    margin-top: 3px;
    font: 400 14.5px/18px "Roboto", sans-serif;
  }
  .contact-panel__services li::before {
    content: "";
    display: inline-block;
    width: 6px; height: 6px;
    border-radius: 50%;
    background: var(--ink-light);
    margin: 0 5px 2px 0;
  }

  .brand-panel {
    flex: 1;
    background: var(--card-white);
    display: flex;
    align-items: center;
    justify-content: center;
    gap: 10px;
    padding-top: 8px;
  }
  .brand-name {
    font: 700 30px/1 "Roboto Condensed", sans-serif;
    color: var(--logo-grey);
  }
  .brand-square {
    width: 18px; height: 18px;
    background: var(--brand-red);
  }
  .brand-name--back {
    font: 700 40px/1 "Roboto Condensed", sans-serif;
    color: var(--ink-light);
  }
</style>
</head>
<body>
  <section class="card card--front">
    <div class="contact-panel">
      <h1 class="contact-panel__name">DALE MARSH</h1>
      <p class="contact-panel__role">CEO/FOUNDER</p>
      <ul class="contact-panel__details">
        <li>Ph : 5307218394</li>
        <li>Dispatch@PipeworksTopMark.example</li>
        <li>www.PipeworksTopMark.example</li>
      </ul>
      <ul class="contact-panel__services">
        <li>Sewer Drain Cleaning</li>
        <li>Maintenance</li>
        <li>Trenchless Pipe Installs</li>
      </ul>
    </div>
    <div class="brand-panel">
      <span class="brand-name">Pipeworks TopMark</span>
      <span class="brand-square"></span>
    </div>
  </section>

  <section class="card card--back">
    <span class="brand-name--back">Pipeworks TopMark</span>
  </section>
</body>
</html>
```